Velvet Lantern rebranding my business with a new business card

I have my new logo and now I need a refresher on my business cards. I really want something fun and fresh. I like black background or anything to make the color pop.
Logo
Name: Velvet Lantern
Contact Info as stated below:
Mira Pellow
555-013-4762
Logo
Name: Velvet Lantern
Mira Pellow
555-013-4762
fb.me/VelvetLanternbyMira
Instagram: @VelvetLanternbyMira

Industry/Entity Type

Business

Contact Information for Business Card

double-sided. Logo on one side. Contact info on the other.

Requirements
Must have
• Logo
• Name: Velvet Lantern
• Contact Info as stated below:
• Mira Pellow
• 555-013-4762
• fb.me/VelvetLanternbyMira
• fb.me/VelvetLanternbyMira

```html
<!DOCTYPE html>
<html lang="en">
<head>
<meta charset="utf-8">
<title>Velvet Lantern – Business Card</title>
<link href="https://fonts.googleapis.com/css2?family=Open+Sans:wght@400;600&display=swap" rel="stylesheet">
<style>
  :root {
    --backdrop: #2a2a2b;
    --card-dark: #141414;
    --card-mid: #2b2b2b;
    --ink: #f4f1f3;
    --blush: #e7b9cc;
    --blush-deep: #c98aa6;
    --ring: #d9a9bd;
  }
  * { margin: 0; padding: 0; box-sizing: border-box; }
  html, body {
    width: 1200px; height: 1015px; overflow: hidden;
    background: var(--backdrop);
    font-family: "Open Sans", Arial, sans-serif;
  }
  .canvas { position: relative; width: 1200px; height: 1015px; }

  .card {
    position: absolute;
    width: 540px; height: 440px;
    border-radius: 26px;
    background: linear-gradient(135deg, var(--card-mid) 0%, var(--card-dark) 55%, #0d0d0d 100%);
    box-shadow: 0 18px 40px rgba(0,0,0,.55);
    overflow: hidden;
  }
  .card-contact { left: 70px; top: 70px; }
  .card-brand { left: 590px; top: 505px; }

  .holder-name {
    position: absolute; left: 48px; top: 118px;
    color: var(--ink); font-size: 40px; font-weight: 400; letter-spacing: .5px;
  }
  .name-rule {
    position: absolute; left: 48px; top: 180px; width: 340px; height: 3px;
    background: var(--blush);
  }
  .contact-list {
    position: absolute; left: 48px; top: 206px; list-style: none;
  }
  .contact-list li {
    display: flex; align-items: center; gap: 12px;
    color: var(--ink); font-size: 20px; line-height: 36px;
  }
  .contact-list svg { width: 20px; height: 20px; flex: none; }
  .contact-list .dot {
    width: 16px; height: 16px; border-radius: 3px; background: var(--blush-deep);
    margin: 0 2px; flex: none;
  }

  .brand-badge {
    position: absolute; left: 386px; top: 92px;
    width: 132px; height: 132px; border-radius: 50%;
    border: 3px solid var(--ring);
    background: #111;
    display: flex; align-items: center; justify-content: center; text-align: center;
  }
  .brand-badge span {
    color: var(--blush); font-size: 17px; font-weight: 600; line-height: 1.15;
  }

  .brand-name {
    position: absolute; inset: 0;
    display: flex; align-items: center; justify-content: center;
    color: var(--blush); font-size: 48px; font-weight: 600; letter-spacing: 1px;
  }
</style>
</head>
<body>
<main class="canvas">

  <section class="card card-contact" aria-label="Contact side">
    <h1 class="holder-name">Mira Pellow</h1>
    <div class="name-rule"></div>
    <ul class="contact-list">
      <li>
        <svg viewBox="0 0 20 20" aria-hidden="true"><path fill="var(--blush-deep)" d="M5 2h3l1.5 4-2 1.5a11 11 0 0 0 5 5L14 10.5l4 1.5v3a2 2 0 0 1-2 2A14 14 0 0 1 3 4a2 2 0 0 1 2-2z"/></svg>
        555-013-4762
      </li>
      <li>
        <svg viewBox="0 0 20 20" aria-hidden="true"><rect x="2" y="4" width="16" height="12" rx="1" fill="var(--blush-deep)"/><path d="M2.5 5l7.5 6 7.5-6" stroke="#141414" stroke-width="1.5" fill="none"/></svg>
        hello@velvetlantern.example
      </li>
      <li><span class="dot"></span>fb.me/VelvetLanternbyMira</li>
      <li><span class="dot"></span>@VelvetLanternbyMira</li>
    </ul>
    <div class="brand-badge"><span>Velvet<br>Lantern</span></div>
  </section>

  <section class="card card-brand" aria-label="Brand side">
    <p class="brand-name">Velvet Lantern</p>
  </section>

</main>
</body>
</html>
```